DJ Colm Vetter

I'm looking for a professional but still artsy/progressive design. I come from a hip hop/club DJ background playing a lot of underground music but have switched to doing more corporate parties and weddings recently. I am all about keeping the dancefloor moving and emotionally connecting with the crowd. I'd like a trendy/updated color palette. Something that's clean enough that looks professional but also trendy enough to convey that by the end of the night we'll be sweatily dancing to the latest hits. Some designers/artists I like: Tarn Olquist, Pavel Remy, Wendell Quarrie, Lumeno 7400, Silas Dravin.

```html
<!DOCTYPE html>
<html lang="en">
<head>
<meta charset="utf-8">
<title>DJ Colm Vetter — Business Card</title>
<link rel="stylesheet" href="https://fonts.googleapis.com/css2?family=Cinzel:wght@400;500&family=Lato:wght@400&display=swap">
<style>
  :root {
    --navy: #074c79;
    --green: #5aa83c;
    --red: #d62a35;
    --white: #ffffff;
    --ink: #1b1b1b;
    --backdrop: #d4d4d4;
  }
  * { margin: 0; padding: 0; box-sizing: border-box; }
  html, body { width: 1200px; height: 802px; overflow: hidden; }
  body { background: var(--backdrop); position: relative; font-family: "Lato", sans-serif; }

  .card {
    position: absolute;
    top: 274px;
    width: 443px;
    height: 264px;
    box-shadow: 0 3px 8px rgba(0,0,0,0.3);
  }
  .card--front { left: 136px; background: var(--white); }
  .card--back { left: 624px; background: var(--navy); display: flex; align-items: center; justify-content: center; }

  .front__band { position: absolute; left: 0; top: 0; width: 50px; height: 100%; background: var(--navy); }
  .front__rule { position: absolute; left: 54px; width: 3px; }
  .front__rule--green { top: 0; height: 105px; background: var(--green); }
  .front__rule--red { top: 113px; bottom: 0; background: var(--red); }

  .wordmark {
    font-family: "Cinzel", serif;
    font-weight: 500;
    letter-spacing: 0.5px;
    white-space: nowrap;
    line-height: 1;
  }
  .front__wordmark { position: absolute; right: 21px; top: 36px; font-size: 25px; color: var(--navy); }
  .back__wordmark { font-size: 36px; color: var(--white); }

  .contact { position: absolute; left: 78px; top: 108px; color: var(--ink); }
  .contact__name { font-family: "Cinzel", serif; font-weight: 500; font-size: 15px; color: var(--navy); letter-spacing: 0.4px; line-height: 17px; }
  .contact__role { font-size: 12.5px; line-height: 15px; margin-bottom: 5px; }
  .contact__list { list-style: none; font-size: 12.5px; }
  .contact__list li { display: flex; align-items: center; gap: 4px; height: 16px; }
  .contact__icon { width: 9px; height: 9px; fill: var(--navy); flex: none; }
  .contact__address { font-size: 12.5px; line-height: 15.5px; margin-top: 5px; }
</style>
</head>
<body>
  <section class="card card--front">
    <div class="front__band"></div>
    <div class="front__rule front__rule--green"></div>
    <div class="front__rule front__rule--red"></div>
    <div class="wordmark front__wordmark">DJ Colm Vetter</div>

    <div class="contact">
      <div class="contact__name">IDRIS CALLOWAY</div>
      <div class="contact__role">Managing Director</div>
      <ul class="contact__list">
        <li><svg class="contact__icon" viewBox="0 0 10 10"><path d="M1 3 Q5 0 9 3 L8 4.5 L6.5 3.8 L6.5 3 Q5 2.6 3.5 3 L3.5 3.8 L2 4.5 Z M2.5 5 H7.5 L8.5 9 H1.5 Z"/></svg>044-123 456 789</li>
        <li><svg class="contact__icon" viewBox="0 0 10 10"><path d="M2.5 0.5 H7.5 V9.5 H2.5 Z M3.5 1.5 V7.5 H6.5 V1.5 Z"/></svg>044-123 456 789</li>
        <li><svg class="contact__icon" viewBox="0 0 10 10"><path d="M0.5 2 H9.5 V8 H0.5 Z M1.5 3 L5 5.5 L8.5 3 Z"/></svg>hello@colmvetter.com</li>
        <li><svg class="contact__icon" viewBox="0 0 10 10"><circle cx="5" cy="5" r="4.5"/></svg>www.colmvetter.com</li>
      </ul>
      <div class="contact__address">12345, Address Goes Here<br>Country Name, 123456.</div>
    </div>
  </section>

  <section class="card card--back">
    <div class="wordmark back__wordmark">DJ Colm Vetter</div>
  </section>
</body>
</html>
```